Looking for a dynamic business card for a pizzeria.

A business card with our food, logo, and space for name, title, email, website, phone. The card should convey quality, unique, amazing. On the front, I envision food photo or photos with the owners names and contact information. On the back, more food with locations, website, facebook, twitter, instagram icons. It should look polished, not cartoonish, or plain.
Target Market(s)
upscale, local food buyers, 30-50 years in age.
Industry/Entity Type
Restaurant
Contact Information for Business Card
Business Name: Bru'nettix, LLC
Website: www.brunettix.com
Back:
2 locations: (can list on the back of card)
1. Harborview
4087 Corlan Avenue
Corvale, WA 98412
360-481-5067
2. Larkspur Hill
7315 Wendmere Road
Corvale, WA 98417
360-293-8840
front:
EDITABLE space for
Business name
Person's Name
title
2nd title
Email address
cell-phone number
Requirements
Must have
- logo
- my food photo or photos (no watermarks showing)
- locations on back
- Person contact information on front
- full bleed

```html
<!DOCTYPE html>
<html lang="en">
<head>
<meta charset="utf-8">
<title>Bru'nettix Business Card</title>
<link rel="stylesheet" href="https://fonts.googleapis.com/css2?family=Questrial&display=swap">
<style>
  :root {
    --canvas-bg: #e9e4dc;
    --card-white: #ffffff;
    --brand-red: #b3141c;
    --brand-green: #2f5a3a;
    --text-dark: #3a3a3a;
    --stitch: rgba(255,255,255,0.75);
    --shadow: rgba(0,0,0,0.18);
  }
  * { box-sizing: border-box; margin: 0; padding: 0; }
  html, body { width: 1200px; height: 950px; overflow: hidden; }
  body {
    background: var(--canvas-bg);
    font-family: "Questrial", "Century Gothic", sans-serif;
    position: relative;
  }
  .card {
    position: absolute;
    top: 115px;
    width: 420px;
    height: 720px;
    background: var(--card-white);
    box-shadow: 0 10px 28px var(--shadow);
    overflow: hidden;
  }
  .card--front { left: 150px; }
  .card--back { left: 630px; }

  /* Front */
  .banner {
    position: absolute;
    left: 30px;
    top: 0;
    width: 370px;
    height: 470px;
  }
  .banner svg { position: absolute; inset: 0; }
  .banner-content {
    position: absolute;
    inset: 30px 30px 0 30px;
    color: #fff;
    text-align: center;
    font-size: 17px;
    line-height: 1.3;
  }
  .person-name { font-size: 24px; letter-spacing: 1px; }
  .person-title { font-size: 17px; margin-bottom: 10px; }
  .divider {
    border: 0;
    border-top: 2px dotted var(--stitch);
    width: 78%;
    margin: 10px auto;
  }
  .location-name { margin-top: 2px; }
  .contact-list { text-align: left; padding-left: 58px; }

  .front-logo {
    position: absolute;
    left: 36px;
    bottom: 110px;
    display: flex;
    align-items: center;
    gap: 14px;
  }
  .brand-name {
    font-family: "Questrial", "Century Gothic", sans-serif;
    color: var(--brand-green);
    font-size: 46px;
    letter-spacing: 1px;
    line-height: 1;
    white-space: nowrap;
  }
  .brand-disc {
    width: 62px;
    height: 62px;
    border-radius: 50%;
    background: var(--brand-red);
    flex: none;
  }

  /* Back */
  .photo-strip {
    position: absolute;
    left: 0;
    width: 100%;
    height: 150px;
  }
  .photo-strip--sandwich { top: 0; background: linear-gradient(160deg, #d9b98a 0%, #9a6a3a 55%, #5c6a3a 100%); }
  .photo-strip--wrap { top: 152px; background: linear-gradient(170deg, #e8dcc0 0%, #7a4a34 50%, #6b9a3e 100%); }
  .photo-strip--tray { top: 304px; background: linear-gradient(180deg, #c9b8a6 0%, #b8553a 55%, #7b3a2a 100%); }

  .back-footer {
    position: absolute;
    left: 0;
    bottom: 0;
    width: 100%;
    height: 266px;
  }
  .social-links {
    position: absolute;
    top: 40px;
    right: 34px;
    display: flex;
    gap: 14px;
  }
  .social-dot {
    width: 22px;
    height: 22px;
    border-radius: 50%;
    background: var(--brand-red);
  }
  .back-logo {
    position: absolute;
    left: 40px;
    bottom: 70px;
  }
  .back-logo .brand-name { font-size: 48px; }
  .website {
    margin-top: 8px;
    color: var(--text-dark);
    font-size: 16px;
    letter-spacing: 1.5px;
  }
</style>
</head>
<body>

  <section class="card card--front">
    <div class="banner">
      <svg width="370" height="470" viewBox="0 0 370 470">
        <polygon points="0,0 370,0 370,410 185,470 0,410" fill="var(--brand-red)"/>
        <polygon points="12,0 358,0 358,402 185,456 12,402" fill="none" stroke="var(--stitch)" stroke-width="2" stroke-dasharray="3 4"/>
      </svg>
      <div class="banner-content">
        <p class="person-name">MARCO DELVANE</p>
        <p class="person-title">Founder</p>
        <hr class="divider">
        <p class="location-name">Harborview</p>
        <p>4087 Corlan Avenue</p>
        <p>Corvale, WA 98412</p>
        <p>Phone:360-481-5067</p>
        <hr class="divider">
        <p class="location-name">Larkspur Hill</p>
        <p>7315 Wendmere Road</p>
        <p>Corvale, WA 98417</p>
        <p>Phone:360-293-8840</p>
        <hr class="divider">
        <div class="contact-list">
          <p>M: 689 512 0476</p>
          <p>E: name@brunettix.com</p>
          <p>W: www.brunettix.com</p>
        </div>
      </div>
    </div>
    <div class="front-logo">
      <span class="brand-name">BRU'NETTIX</span>
      <span class="brand-disc"></span>
    </div>
  </section>

  <section class="card card--back">
    <div class="photo-strip photo-strip--sandwich" role="img" aria-label="Photo of a toasted panini sandwich with greens"></div>
    <div class="photo-strip photo-strip--wrap" role="img" aria-label="Photo of a flatbread wrap with sliced steak, peppers and red onion"></div>
    <div class="photo-strip photo-strip--tray" role="img" aria-label="Photo of a tray of baked appetizer bites"></div>
    <div class="back-footer">
      <div class="social-links">
        <span class="social-dot"></span>
        <span class="social-dot"></span>
      </div>
      <div class="back-logo">
        <p class="brand-name">BRU'NETTIX</p>
        <p class="website">www.brunettix.com</p>
      </div>
    </div>
  </section>

</body>
</html>
```